Harbor Crestline (Business Card Design)

Need business cards designed. Something modern, chic, and sleek. Mabye the back of the card should be the navy blue that is in the logo and then just the logo on the back.

Target Market(s)

Those in the hotel, office, and renovation industry

Contact Information for Business Card

1. Logo 2. Dorian Fenwick 3. CEO/Founder 4. Phone: (833) HarbCre / (833) 427-2731 5. Email: dorian@theharborcrestline.com 6. Website: www.theharborcrestline.com

Font styles to use
Other font styles liked:
• Look at the logo font and base the font for everything else off of that.

Colors
0054AA
0677BA
7BADD7
CADEEF
E8F1F8

Requirements
Must have
• Colors that are associated in the logo
Nice to have
• Sleek modern clean and chic design.

```html
<!DOCTYPE html>
<html lang="en">
<head>
<meta charset="utf-8">
<title>Harbor Crestline — Business Card</title>
<link rel="stylesheet" href="https://fonts.googleapis.com/css2?family=Montserrat:wght@500&family=Open+Sans:wght@400;700&display=swap">
<style>
  :root {
    --backdrop: #2a2b30;
    --navy: #0f1a45;
    --gold: #cfa54a;
    --white: #ffffff;
  }
  * { margin: 0; padding: 0; box-sizing: border-box; }
  html, body { width: 1200px; height: 947px; overflow: hidden; }
  body { background: var(--backdrop); position: relative; font-family: "Open Sans", sans-serif; }

  .card {
    position: absolute;
    width: 620px; height: 354px;
    background: var(--navy);
    border-radius: 22px;
    overflow: hidden;
    box-shadow: 0 18px 40px rgba(0,0,0,.45);
  }
  .card--front { left: 60px; top: 80px; }
  .card--back  { left: 520px; top: 513px; }

  .wordmark {
    display: flex; align-items: center; gap: 14px;
    font-family: "Montserrat", sans-serif; font-weight: 500;
    color: var(--white); letter-spacing: .12em; text-transform: uppercase;
  }
  .wordmark__square { width: 12px; height: 12px; background: var(--gold); flex: none; }

  .card--front .wordmark {
    position: absolute; left: 0; right: 0; top: 0; bottom: 0;
    justify-content: center; font-size: 34px;
  }

  .card--back .wordmark {
    position: absolute; left: 34px; top: 120px; width: 200px;
    font-size: 21px; line-height: 1.25; gap: 10px;
  }

  .divider {
    position: absolute; left: 258px; top: 62px;
    width: 1.5px; height: 170px; background: var(--gold);
  }

  .contact { position: absolute; left: 286px; top: 56px; color: var(--white); z-index: 1; }
  .contact__name { color: var(--gold); font-weight: 700; font-size: 27px; line-height: 1.1; }
  .contact__title { font-size: 17px; margin-top: 2px; }
  .contact__list { list-style: none; margin-top: 20px; }
  .contact__item { display: flex; align-items: center; gap: 9px; font-size: 15px; line-height: 1.5; }
  .contact__item svg { width: 13px; height: 13px; flex: none; fill: var(--gold); }

  .wave { position: absolute; left: 0; bottom: 0; width: 620px; height: 354px; }
</style>
</head>
<body>

<section class="card card--front" aria-label="Card front">
  <div class="wordmark"><span class="wordmark__square"></span>Harbor Crestline</div>
</section>

<section class="card card--back" aria-label="Card back">
  <svg class="wave" viewBox="0 0 620 354" aria-hidden="true">
    <path d="M0 322 C 300 318, 520 290, 620 150 L620 354 L0 354 Z" fill="var(--white)"/>
    <path d="M0 330 C 302 326, 524 298, 620 162 L620 354 L0 354 Z" fill="var(--navy)"/>
    <path d="M0 338 C 305 334, 528 306, 620 172 L620 354 L0 354 Z" fill="var(--gold)"/>
  </svg>

  <div class="wordmark"><span class="wordmark__square"></span>Harbor Crestline</div>

  <div class="divider"></div>

  <div class="contact">
    <p class="contact__name">Dorian Fenwick</p>
    <p class="contact__title">Founder + CEO</p>
    <ul class="contact__list">
      <li class="contact__item">
        <svg viewBox="0 0 24 24"><path d="M6.6 10.8a15.1 15.1 0 0 0 6.6 6.6l2.2-2.2a1 1 0 0 1 1-.25 11.4 11.4 0 0 0 3.6.57 1 1 0 0 1 1 1V20a1 1 0 0 1-1 1A17 17 0 0 1 3 4a1 1 0 0 1 1-1h3.5a1 1 0 0 1 1 1c0 1.25.2 2.45.57 3.57a1 1 0 0 1-.25 1z"/></svg>
        (833) 427-2731
      </li>
      <li class="contact__item">
        <svg viewBox="0 0 24 24"><path d="M2 5h20v14H2z M2 5l10 8 10-8" fill="none" stroke="var(--gold)" stroke-width="2.4"/></svg>
        dorian@theharborcrestline.com
      </li>
      <li class="contact__item">
        <svg viewBox="0 0 24 24"><circle cx="12" cy="12" r="9" fill="none" stroke="var(--gold)" stroke-width="2.2"/><path d="M3 12h18M12 3c3 3 3 15 0 18M12 3c-3 3-3 15 0 18" fill="none" stroke="var(--gold)" stroke-width="1.8"/></svg>
        www.theharborcrestline.com
      </li>
    </ul>
  </div>
</section>

</body>
</html>
```